Bureau for Innovation and Outreach Needs a Graphically Designed Powerpoint Template

We are from Bureau for Innovation and Outreach (BIO), part of a medical school. BIO contributes to the medical school by overseeing and managing intellectual property generated by researchers at the medical school, and also works to ensure optimal commercial outcomes for all inventions arising from the medical school. We want a graphically designed powerpoint presentation template to describe how BIO is involved in a researcher’s journey to major scientific contributions. The journey should be represented in the form of a main road (or pathway). Along the main road, there will be smaller roads branching out, each representing one of the researcher’s major scientific contributions. We will be inputting text details of each major scientific contribution near each of the small road branches. The smaller road branches will also need to be removable / editable. This is because we might need to send the template to different researchers to input details of their major scientific contributions, and each researcher will have a different number of them. Hence, you can possibly place around 6 branches along the main road, but we want to be able to remove the branches should we need to. Removal of the branches (design elements) should still result in a seamless image in powerpoint. We also want to be able to add and edit text in the design template. The start of the main road should contain a placeholder for us to place the researcher’s photo. The end of the road will lead to one of the major scientific contributions. Please see the uploaded sketch to have an idea of what we are looking to get. We welcome deviations and changes to the design as shown from the sketch, as long as the design is able to convey what we have described above. As this powerpoint template will be used for presentation to the senior management, we need it to look beautiful yet professional.

Target Market(s)

Researcher, Scientist

Industry/Entity Type

School

Font styles to use
Serif
Sans Serif

Requirements
Must have
• A main road or pathway as mentioned in the project description.
Nice to have
• We will leave the "nice to haves" to be decided by the designer.
Should not have
• Trees

```html
<!DOCTYPE html>
<html lang="en">
<head>
<meta charset="utf-8">
<title>Design Idea 03 – Research Journey Template</title>
<link href="https://fonts.googleapis.com/css2?family=Arimo:wght@700&family=Patrick+Hand&display=swap" rel="stylesheet">
<style>
  :root{
    --board:#412c2e;
    --title:#6b6b6b;
    --map-light:#f1f1f1;
    --map-grey:#e2e2e2;
    --lime:#c6e000;
    --water:#5dd6f4;
    --road:#4cc93a;
    --road-line:#ffffff;
    --wood:#b7763d;
    --wood-dark:#7a4a22;
    --paper:#fbf5e3;
    --ink:#1e1a16;
    --paper-ink:#fff8e8;
    --photo:#3a3a3a;
  }
  *{margin:0;padding:0;box-sizing:border-box}
  html,body{width:1200px;height:1200px;overflow:hidden;background:var(--board)}
  .board{position:relative;width:1200px;height:1200px}
  .board-title{
    position:absolute;left:0;top:34px;width:1136px;text-align:center;
    font-family:"Arimo",Arial,sans-serif;font-weight:700;font-size:44px;
    color:var(--title);letter-spacing:1px;
  }
  .slide{position:absolute;left:136px;width:902px;height:508px;display:block}
  .slide--a{top:118px}
  .slide--b{top:642px}

  .road{fill:none;stroke:var(--road);stroke-width:18;stroke-linecap:round}
  .road-line{fill:none;stroke:var(--road-line);stroke-width:1.6;stroke-dasharray:7 6}

  .sign-wood{fill:var(--wood);stroke:var(--wood-dark);stroke-width:2}
  .sign-paper{fill:var(--paper);stroke:var(--wood-dark);stroke-width:3}
  .photo-frame{fill:var(--paper)}
  .photo{fill:var(--photo)}

  .sign-text{font-family:"Patrick Hand",cursive;font-size:17px;text-anchor:middle}
  .sign-text--dark{fill:var(--ink)}
  .sign-text--light{fill:var(--paper-ink)}
  .award-text{font-family:"Patrick Hand",cursive;font-size:20px;fill:var(--ink);text-anchor:middle;letter-spacing:1px}
  .name{font-family:"Patrick Hand",cursive;font-size:17px;fill:var(--ink);text-anchor:middle}
  .degree{font-family:"Patrick Hand",cursive;font-size:11px;fill:var(--ink);text-anchor:middle}
</style>
</head>
<body>
<main class="board">
  <h1 class="board-title">DESIGN IDEA - 03</h1>

  <svg width="0" height="0" style="position:absolute" aria-hidden="true">
    <defs>
      <linearGradient id="backdrop-a" x1="0" y1="1" x2="1" y2="0">
        <stop offset="0" stop-color="#dbe98a"/>
        <stop offset="0.25" stop-color="#f1f1f1"/>
        <stop offset="0.75" stop-color="#e6e6e6"/>
        <stop offset="1" stop-color="#d3e66a"/>
      </linearGradient>
      <linearGradient id="backdrop-b" x1="0" y1="0" x2="1" y2="1">
        <stop offset="0" stop-color="#e9ef c0"/>
        <stop offset="0" stop-color="#e4ecb0"/>
        <stop offset="0.35" stop-color="#f1f1f1"/>
        <stop offset="0.7" stop-color="#e6e6e6"/>
        <stop offset="1" stop-color="#a9e4f2"/>
      </linearGradient>

      <g id="journey">
        <path class="road" d="M217,197 C270,200 285,230 290,280 C295,330 320,352 370,352 L970,352 C1020,352 1040,380 1040,432"/>
        <path class="road-line" d="M217,197 C270,200 285,230 290,280 C295,330 320,352 370,352 L970,352 C1020,352 1040,380 1040,432"/>
        <g class="branch">
          <path class="road" d="M350,352 C400,352 420,320 420,282"/>
          <path class="road-line" d="M350,352 C400,352 420,320 420,282"/>
        </g>
        <g class="branch">
          <path class="road" d="M580,352 C630,352 650,320 650,282"/>
          <path class="road-line" d="M580,352 C630,352 650,320 650,282"/>
        </g>
        <g class="branch">
          <path class="road" d="M845,352 C895,352 915,320 915,282"/>
          <path class="road-line" d="M845,352 C895,352 915,320 915,282"/>
        </g>
        <g class="branch">
          <path class="road" d="M350,352 C385,352 400,380 400,407"/>
          <path class="road-line" d="M350,352 C385,352 400,380 400,407"/>
        </g>
        <g class="branch">
          <path class="road" d="M570,352 C605,352 615,390 615,427"/>
          <path class="road-line" d="M570,352 C605,352 615,390 615,427"/>
        </g>
        <g class="branch">
          <path class="road" d="M760,352 C795,352 805,390 805,427"/>
          <path class="road-line" d="M760,352 C795,352 805,390 805,427"/>
        </g>

        <path class="sign-paper" d="M115,32 L210,32 L232,58 L210,86 L115,86 Z"/>
        <text class="award-text" x="166" y="55">START</text>
        <text class="award-text" x="166" y="76">AWARD</text>

        <rect class="photo-frame" x="56" y="144" width="160" height="152"/>
        <rect class="photo" x="62" y="150" width="148" height="140" role="img" aria-label="Researcher portrait photo placeholder"/>
        <text class="name" x="139" y="318">Daniel Hartley</text>
        <text class="degree" x="139" y="332">MD, Ph.D</text>

        <rect class="sign-paper" x="370" y="130" width="118" height="90"/>
        <text class="sign-text sign-text--dark" x="429" y="172">BIO XYZ</text>
        <text class="sign-text sign-text--dark" x="429" y="191">Project</text>

        <rect class="sign-wood" x="598" y="132" width="110" height="76"/>
        <text class="sign-text sign-text--light" x="653" y="163">BIO XYZ</text>
        <text class="sign-text sign-text--light" x="653" y="182">Project</text>

        <g transform="rotate(-8 906 178)">
          <rect class="sign-paper" x="843" y="130" width="127" height="96"/>
          <text class="sign-text sign-text--dark" x="906" y="157">Major Science</text>
          <text class="sign-text sign-text--dark" x="906" y="175">Fiction</text>
          <text class="sign-text sign-text--dark" x="906" y="193">Contribution</text>
          <text class="sign-text sign-text--dark" x="906" y="211"># 3</text>
        </g>

        <g transform="rotate(3 397 447)">
          <rect class="sign-wood" x="341" y="405" width="113" height="84"/>
          <text class="sign-text sign-text--light" x="397" y="428">Major Science</text>
          <text class="sign-text sign-text--light" x="397" y="446">Fiction</text>
          <text class="sign-text sign-text--light" x="397" y="464">Contribution</text>
          <text class="sign-text sign-text--light" x="397" y="482"># 1</text>
        </g>

        <g transform="rotate(4 614 470)">
          <rect class="sign-paper" x="551" y="422" width="126" height="96"/>
          <text class="sign-text sign-text--dark" x="614" y="450">Major Science</text>
          <text class="sign-text sign-text--dark" x="614" y="468">Fiction</text>
          <text class="sign-text sign-text--dark" x="614" y="486">Contribution</text>
          <text class="sign-text sign-text--dark" x="614" y="504"># 2</text>
        </g>

        <g transform="rotate(-3 812 464)">
          <rect class="sign-wood" x="755" y="422" width="114" height="84"/>
          <text class="sign-text sign-text--light" x="812" y="444">Major Science</text>
          <text class="sign-text sign-text--light" x="812" y="462">Fiction</text>
          <text class="sign-text sign-text--light" x="812" y="480">Contribution</text>
          <text class="sign-text sign-text--light" x="812" y="498"># 4</text>
        </g>

        <rect class="sign-wood" x="937" y="432" width="178" height="85"/>
        <rect class="sign-paper" x="966" y="441" width="118" height="68"/>
        <text class="sign-text sign-text--dark" x="1025" y="461">Major Science</text>
        <text class="sign-text sign-text--dark" x="1025" y="479">Fiction</text>
        <text class="sign-text sign-text--dark" x="1025" y="497">Contribution</text>
      </g>
    </defs>
  </svg>

  <svg class="slide slide--a" viewBox="0 0 1127 635" role="group" aria-label="Research journey slide, layout A">
    <rect width="1127" height="635" fill="url(#backdrop-a)" role="img" aria-label="Stylised city map backdrop with green park areas"/>
    <use href="#journey"/>
  </svg>

  <svg class="slide slide--b" viewBox="0 0 1127 635" role="group" aria-label="Research journey slide, layout B">
    <rect width="1127" height="635" fill="url(#backdrop-b)" role="img" aria-label="Stylised park map backdrop with lake"/>
    <use href="#journey"/>
  </svg>
</main>
</body>
</html>
```